Design material for Lumora Event

We need a design of POSM for Lumora Event
1. Content:
- The Lumora Event 3rd
- Singapore 28.10.2018
- A placeholder for insert logo of sponsors (limit 10 logo)
2. POSM:
- Backdrop: 5,5m and 2,6m
- Banner: 4m and 0,5m
- Standee: 0,8m and 2m
- Cover: A4 size
3. Style:
We need style simply because we are a hospital.
Main color: light blue and a little of green (if can)

Hope to see your design soon!

Font styles to use
Sans Serif

Colors
0792cd
85cae6
86cfc6
33b8a4
33a6d7

```html
<!DOCTYPE html>
<html lang="en">
<head>
<meta charset="utf-8">
<title>Lumora Event 2018 Singapore – Banner</title>
<link rel="stylesheet" href="https://fonts.googleapis.com/css2?family=Nunito:ital,wght@0,600;0,800;0,900;1,900&display=swap">
<style>
  :root {
    --blue-deep: #0792cd;
    --blue-light: #85cae6;
    --green-soft: #86cfc6;
    --green-strong: #33b8a4;
    --blue-mid: #33a6d7;
    --title-ink: #0b6a8c;
    --sponsor-ink: #2f4f5e;
    --paper: #ffffff;
  }
  html, body {
    margin: 0;
    padding: 0;
    overflow: hidden;
    background: var(--paper);
  }
  .banner {
    position: relative;
    width: 1200px;
    height: 151px;
    background: var(--paper);
    overflow: hidden;
    font-family: "Nunito", sans-serif;
  }
  .sponsors {
    position: absolute;
    top: 0;
    width: 300px;
    height: 151px;
  }
  .sponsors--left { left: 22px; }
  .sponsors--right { left: 860px; }
  .sponsor-row {
    position: absolute;
    left: 0;
    right: 0;
    display: flex;
    align-items: center;
    justify-content: space-between;
  }
  .sponsor-row--top { top: 40px; }
  .sponsor-row--bottom { top: 103px; padding-left: 10px; }
  .sponsor {
    display: flex;
    align-items: center;
    gap: 3px;
    font-weight: 800;
    font-size: 8.5px;
    line-height: 1;
    color: var(--sponsor-ink);
    white-space: nowrap;
  }
  .sponsor__mark {
    width: 7px;
    height: 7px;
    background: var(--blue-mid);
  }
  .sponsor__mark--round { border-radius: 50%; background: var(--green-strong); }
  .event-panel {
    position: absolute;
    left: 364px;
    top: 0;
    width: 467px;
    height: 151px;
  }
  .event-panel svg { display: block; }
  .event-title {
    font-family: "Nunito", sans-serif;
    font-weight: 900;
    fill: var(--title-ink);
  }
  .event-edition {
    font-family: "Nunito", sans-serif;
    font-weight: 900;
    fill: var(--paper);
  }
  .event-year {
    font-family: "Nunito", sans-serif;
    font-weight: 900;
    font-style: italic;
    fill: var(--title-ink);
  }
  .event-city {
    font-family: "Nunito", sans-serif;
    font-weight: 800;
    fill: var(--paper);
    letter-spacing: 5px;
  }
</style>
</head>
<body>
  <div class="banner">

    <div class="sponsors sponsors--left">
      <div class="sponsor-row sponsor-row--top">
        <span class="sponsor"><span class="sponsor__mark"></span>Bluecrest</span>
        <span class="sponsor">Pinewell</span>
        <span class="sponsor"><span class="sponsor__mark sponsor__mark--round"></span>Fernhollow</span>
        <span class="sponsor">Zentra</span>
        <span class="sponsor">Harbor</span>
        <span class="sponsor">Riverline<br>Paddle</span>
      </div>
      <div class="sponsor-row sponsor-row--bottom">
        <span class="sponsor">Riverline<br>Paddle</span>
        <span class="sponsor"><span class="sponsor__mark"></span>Trekwise</span>
        <span class="sponsor">Summitra</span>
        <span class="sponsor">Westwave</span>
        <span class="sponsor">Corelyn</span>
        <span class="sponsor"><span class="sponsor__mark"></span>Vantro</span>
      </div>
    </div>

    <div class="event-panel">
      <svg width="467" height="151" viewBox="0 0 467 151" xmlns="http://www.w3.org/2000/svg">
        <defs>
          <linearGradient id="skyline-tone" x1="0" y1="0" x2="0" y2="1">
            <stop offset="0" stop-color="#f4f4f4"/>
            <stop offset="0.55" stop-color="#b9b9b9"/>
            <stop offset="1" stop-color="#e6e6e6"/>
          </linearGradient>
        </defs>
        <rect class="skyline-photo" x="150" y="0" width="317" height="110" fill="url(#skyline-tone)" role="img" aria-label="Greyscale photo of the Singapore skyline with waterfront towers and domes"/>
        <path class="wave-green" d="M0 0 H52 C120 55 230 112 370 110 C410 110 440 104 467 96 V151 H0 Z" fill="var(--green-soft)"/>
        <path class="wave-blue" d="M175 151 C290 138 385 105 467 58 V151 Z" fill="var(--blue-light)" stroke="var(--paper)" stroke-width="5"/>
        <text class="event-edition" x="14" y="103" font-size="46">3</text>
        <text class="event-edition" x="40" y="70" font-size="13">rd</text>
        <text class="event-title" x="58" y="94" font-size="25">Lumora</text>
        <text class="event-title" x="58" y="119" font-size="25">Event</text>
        <text class="event-year" x="380" y="113" font-size="23">2018</text>
        <text class="event-city" x="345" y="139" font-size="12">SINGAPORE</text>
      </svg>
    </div>

    <div class="sponsors sponsors--right">
      <div class="sponsor-row sponsor-row--top">
        <span class="sponsor"><span class="sponsor__mark"></span>Bluecrest</span>
        <span class="sponsor">Pinewell</span>
        <span class="sponsor"><span class="sponsor__mark sponsor__mark--round"></span>Fernhollow</span>
        <span class="sponsor">Zentra</span>
        <span class="sponsor">Harbor</span>
        <span class="sponsor">Riverline<br>Paddle</span>
      </div>
      <div class="sponsor-row sponsor-row--bottom">
        <span class="sponsor">Riverline<br>Paddle</span>
        <span class="sponsor"><span class="sponsor__mark"></span>Trekwise</span>
        <span class="sponsor">Summitra</span>
        <span class="sponsor">Westwave</span>
        <span class="sponsor">Corelyn</span>
        <span class="sponsor"><span class="sponsor__mark"></span>Vantro</span>
      </div>
    </div>

  </div>
</body>
</html>
```